Chimney Service company needs new business card design

We need a updated business card with our new logo added. We provide a full range of chimney services throughout Vermont and New Hampshire. The business card will be one sided and color. Attached is our current business card another document showing all the information we would like on the card.
We dont like a lot of flashy colors.... here is a link to our website to get an idea of our branding www.flueguardianvt.example

Target Market(s)

homeowners

Industry/Entity Type

Business

Contact Information for Business Card

See attached sheet for content.

Font styles to use
Serif
Sans Serif

Requirements
Must have
• all information provided on separate sheet
Should not have
• Additional information that may clogg up design

```html
<!DOCTYPE html>
<html lang="en">
<head>
<meta charset="utf-8">
<title>Flue Guardian – Business Card</title>
<link href="https://fonts.googleapis.com/css2?family=Cinzel:wght@400;600&family=Lato:wght@400;700&display=swap" rel="stylesheet">
<style>
  :root {
    --backdrop: #34302d;
    --card: #121212;
    --silver: #d9d9d9;
    --silver-dim: #a9a9a9;
    --accent-red: #b3201f;
    --text: #eeeeee;
  }
  * { margin: 0; padding: 0; box-sizing: border-box; }
  html, body { width: 1200px; height: 900px; overflow: hidden; }
  body {
    background: var(--backdrop);
    display: flex;
    flex-direction: column;
    align-items: center;
    justify-content: center;
    gap: 40px;
    font-family: "Lato", Arial, sans-serif;
  }
  .card {
    width: 700px;
    height: 400px;
    background: var(--card);
    position: relative;
    box-shadow: 0 12px 30px rgba(0,0,0,.45);
  }

  /* Front: details */
  .brand-mark {
    position: absolute; left: 50px; top: 70px;
    display: flex; align-items: center; gap: 16px;
  }
  .brand-square {
    width: 74px; height: 74px;
    border: 7px solid var(--silver);
  }
  .brand-name {
    font-family: "Cinzel", Georgia, serif;
    font-size: 26px; color: var(--silver); letter-spacing: 1px;
  }
  .service-area {
    position: absolute; left: 50px; top: 180px;
    font-family: "Cinzel", Georgia, serif;
    font-size: 17px; color: var(--silver); letter-spacing: .5px;
  }
  .service-list {
    position: absolute; left: 50px; top: 222px;
    list-style: none;
  }
  .service-list li {
    font-size: 18px; color: var(--text); line-height: 28px;
    display: flex; align-items: center; gap: 14px;
  }
  .service-list li::before {
    content: ""; width: 10px; height: 10px; background: var(--accent-red);
  }
  .credentials {
    position: absolute; right: 40px; top: 40px;
    text-align: right; font-size: 16px; color: var(--text); line-height: 26px;
  }
  .credentials .divider { color: var(--accent-red); margin: 0 6px; }
  .contact {
    position: absolute; right: 40px; top: 240px;
    list-style: none; text-align: right;
  }
  .contact li {
    font-size: 16px; color: var(--text); line-height: 28px;
    display: flex; justify-content: flex-end; align-items: center; gap: 8px;
  }
  .contact svg { width: 14px; height: 14px; }

  /* Back: logo side */
  .card-back { display: flex; flex-direction: column; align-items: center; justify-content: center; }
  .back-square {
    width: 100px; height: 100px;
    border: 9px solid var(--silver);
    margin-bottom: 26px;
  }
  .back-name {
    font-family: "Cinzel", Georgia, serif;
    font-size: 36px; color: var(--silver); letter-spacing: 2px;
  }
  .founded {
    display: flex; align-items: center; gap: 12px; margin-top: 4px;
    font-family: "Cinzel", Georgia, serif; font-size: 14px; color: var(--silver); letter-spacing: 2px;
  }
  .founded .rule { width: 110px; height: 2px; background: var(--silver-dim); }
</style>
</head>
<body>
  <section class="card card-front">
    <div class="brand-mark">
      <div class="brand-square"></div>
      <span class="brand-name">Flue Guardian</span>
    </div>
    <p class="service-area">Serving VT and New Hampshire since 1989</p>
    <ul class="service-list">
      <li>Full Masonry Services</li>
      <li>Historic chimney restoration</li>
      <li>Stainless steel liners</li>
      <li>New Chimney installations</li>
      <li>CSIA Certified Chimney sweeps</li>
    </ul>
    <div class="credentials">
      <p>Fully Insured<span class="divider">|</span>Free Estimates</p>
      <p>Family owned and operated</p>
    </div>
    <ul class="contact">
      <li>802-555-0147
        <svg viewBox="0 0 16 16" aria-hidden="true"><path fill="#b3201f" d="M3 1l3 3-2 2c1 2 3 4 5 5l2-2 3 3-2 3C6 15 1 10 0 3z"/></svg>
      </li>
      <li>info@flueguardianvt.example
        <svg viewBox="0 0 16 16" aria-hidden="true"><rect x="1" y="3" width="14" height="10" fill="#b3201f"/><path d="M1 3l7 6 7-6" stroke="#121212" stroke-width="1.5" fill="none"/></svg>
      </li>
      <li>www.flueguardianvt.example
        <svg viewBox="0 0 16 16" aria-hidden="true"><circle cx="8" cy="8" r="7" fill="#b3201f"/><path d="M1 8h14M8 1c-3 4-3 10 0 14M8 1c3 4 3 10 0 14" stroke="#121212" stroke-width="1.2" fill="none"/></svg>
      </li>
    </ul>
  </section>

  <section class="card card-back">
    <div class="back-square"></div>
    <p class="back-name">Flue Guardian</p>
    <div class="founded"><span class="rule"></span>Inc 1989<span class="rule"></span></div>
  </section>
</body>
</html>
```